Business card for Sports Apparel business

DOUBLE SIDED DESIGN
We need business cards for a new sports apparel business. We are developing a protective headband for soccer initially.
Torvalle is focused on designing and developing head protection products to reduce the likelihood of concussion when playing sports. Exploring and understanding medical insights, material science research, current and former players experiences and governing bodies guidelines has allowed Torvalle to develop the safety, style, form and function requirements of a suitable product to bring to market.
Target Market(s)
Mums buying kits for the sons and daughters. Amateur footballers.
Industry/Entity Type
Sporting Good
Contact Information for Business Card
Martin Ashworth - CEO
Mobile: +44 7431589027
Email: martin@torvalle.co.uk
Tel: 0208 5519372
Helena Pargeter - COO
Mob: +44 7385 640117
Email: helena@torvalle.co.uk
Tel: 0208 5519372
Duncan Farrow - CCO
Mob: +44 7564 293081
Email: duncan@torvalle.co.uk
Tel: 0208 5519372
Look and feel
Each slider illustrates characteristics of the customer's brand and the style your logo design should communicate.

```html
<!DOCTYPE html>
<html lang="en">
<head>
<meta charset="utf-8">
<title>Torvalle Business Card</title>
<link rel="stylesheet" href="https://fonts.googleapis.com/css2?family=Montserrat:wght@400;600;700&display=swap">
<style>
  :root {
    --backdrop: #1b1b1c;
    --card-grey: #666667;
    --band-slate: #56687a;
    --accent-blue: #1f5f9e;
    --ink-white: #ffffff;
    --wordmark-silver: #d9dadc;
    --rule: #e6e6e6;
  }
  * { margin: 0; padding: 0; box-sizing: border-box; }
  html, body {
    width: 1200px; height: 900px; overflow: hidden;
    background: var(--backdrop);
    font-family: "Montserrat", sans-serif;
  }
  .stage {
    position: relative; width: 1200px; height: 900px;
    display: flex; flex-direction: column; align-items: center; justify-content: center; gap: 40px;
  }
  .card {
    position: relative; width: 580px; height: 332px;
    background: var(--card-grey); overflow: hidden;
  }
  /* Back side */
  .band { position: absolute; background: var(--band-slate); }
  .band--top { left: 0; right: 0; top: 0; height: 26px; }
  .band--bottom { left: 0; right: 0; bottom: 0; height: 26px; }
  .wordmark {
    display: flex; align-items: center; gap: 14px;
    font-weight: 600; letter-spacing: 2px; text-transform: uppercase;
  }
  .wordmark__square { display: block; background: currentColor; }
  .card--back .wordmark {
    position: absolute; left: 50%; top: 50%; transform: translate(-50%, -50%);
    color: var(--wordmark-silver); font-size: 52px;
  }
  .card--back .wordmark__square { width: 30px; height: 30px; }
  /* Front side */
  .card--front .wordmark {
    position: absolute; left: 50%; top: 58px; transform: translateX(-50%);
    color: var(--ink-white); font-size: 48px;
  }
  .card--front .wordmark__square { width: 28px; height: 28px; }
  .divider {
    position: absolute; left: 60px; right: 60px; top: 168px;
    height: 1px; background: var(--rule);
  }
  .person { position: absolute; left: 60px; top: 184px; color: var(--ink-white); }
  .person__name { font-weight: 700; font-size: 17px; letter-spacing: 1px; text-transform: uppercase; }
  .person__role { font-weight: 400; font-size: 16px; margin-top: 2px; }
  .contacts {
    position: absolute; right: 60px; bottom: 38px;
    list-style: none; color: var(--ink-white); font-size: 17px; font-weight: 400;
    text-align: right; line-height: 27px;
  }
  .contacts li { display: flex; align-items: center; justify-content: flex-end; gap: 10px; }
  .contacts svg { width: 16px; height: 16px; fill: none; stroke: var(--ink-white); stroke-width: 1.6; }
  .accent-bar {
    position: absolute; left: 40px; bottom: 0; width: 250px; height: 8px;
    background: var(--accent-blue);
  }
</style>
</head>
<body>
<main class="stage">
  <section class="card card--back" aria-label="Card back">
    <div class="band band--top"></div>
    <div class="band band--bottom"></div>
    <div class="wordmark"><span class="wordmark__square"></span>Torvalle</div>
  </section>

  <section class="card card--front" aria-label="Card front">
    <div class="wordmark"><span class="wordmark__square"></span>Torvalle</div>
    <div class="divider"></div>
    <div class="person">
      <p class="person__name">Martin Ashworth</p>
      <p class="person__role">CEO</p>
    </div>
    <ul class="contacts">
      <li>0208 551 9372
        <svg viewBox="0 0 16 16"><rect x="4" y="1.5" width="8" height="13" rx="1.5"/><line x1="7" y1="12" x2="9" y2="12"/></svg>
      </li>
      <li>+44 7431589027
        <svg viewBox="0 0 16 16"><path d="M3 2.5l3 0.5 1 3-1.8 1.3a8 8 0 0 0 3.5 3.5L10 9l3 1 0.5 3c-1 1-2 1.5-3 1.2C6.5 13 3 9.5 1.8 5.5 1.5 4.5 2 3.5 3 2.5z"/></svg>
      </li>
      <li>martin@torvalle.co.uk
        <svg viewBox="0 0 16 16"><rect x="1.5" y="3.5" width="13" height="9"/><path d="M1.5 3.5l6.5 5 6.5-5"/></svg>
      </li>
    </ul>
    <div class="accent-bar"></div>
  </section>
</main>
</body>
</html>
```